Personal letterhead and stationary

I am looking for someone to design letterhead and stationary set for my personal use. I want something simple and timeless with a little bit of color. I like photography, computers and writing.

```html
<!DOCTYPE html>
<html lang="en">
<head>
<meta charset="utf-8">
<title>Thomas Gale Ward — Letterhead</title>
<link rel="stylesheet" href="https://fonts.googleapis.com/css2?family=Josefin+Slab:wght@300;400;600&display=swap">
<style>
  :root {
    --paper: #efe0c7;
    --ink: #2a2826;
    --rule: #4a4540;
    --signature-tone: #fbf5ea;
  }
  * { margin: 0; padding: 0; box-sizing: border-box; }
  html, body { width: 848px; height: 1200px; overflow: hidden; background: var(--paper); }
  .letterhead {
    position: relative;
    width: 848px;
    height: 1200px;
    background: var(--paper);
    color: var(--ink);
    font-family: "Josefin Slab", Georgia, serif;
  }
  .header-rule {
    position: absolute;
    top: 140px;
    height: 8px;
    border-top: 1px solid var(--rule);
    border-bottom: 1px solid var(--rule);
  }
  .header-rule--left { left: 93px; width: 250px; }
  .header-rule--right { left: 495px; width: 285px; }
  .owner-name {
    position: absolute;
    left: 98px;
    top: 106px;
    font-size: 23px;
    font-weight: 400;
    letter-spacing: 0.5px;
    text-transform: uppercase;
  }
  .owner-email {
    position: absolute;
    left: 96px;
    top: 152px;
    font-size: 12.5px;
    font-weight: 400;
  }
  .owner-phone {
    position: absolute;
    right: 86px;
    top: 110px;
    font-size: 19px;
    font-weight: 300;
    display: flex;
    align-items: center;
    gap: 6px;
  }
  .owner-phone svg { width: 16px; height: 20px; fill: var(--ink); }
  .owner-address {
    position: absolute;
    right: 69px;
    top: 152px;
    font-size: 12.5px;
    font-weight: 400;
  }
  .name-mark {
    position: absolute;
    left: 343px;
    width: 152px;
    top: 132px;
    height: 24px;
    display: flex;
    align-items: center;
    justify-content: center;
    gap: 6px;
    font-size: 12px;
    font-weight: 400;
    letter-spacing: 0.5px;
    text-transform: uppercase;
  }
  .name-mark__dot {
    width: 12px; height: 12px;
    border-radius: 50%;
    background: var(--ink);
  }
  .signature {
    position: absolute;
    left: 528px;
    top: 940px;
    width: 278px;
    height: 128px;
    border-radius: 40px;
    background: radial-gradient(ellipse at center, var(--signature-tone) 0%, rgba(251,245,234,0) 72%);
    opacity: 0.8;
  }
</style>
</head>
<body>
<main class="letterhead">
  <header class="letterhead-header">
    <div class="header-rule header-rule--left"></div>
    <div class="header-rule header-rule--right"></div>

    <h1 class="owner-name">Thomas Gale Ward</h1>
    <p class="owner-email">thomas@mailbox.com.au</p>

    <div class="name-mark">
      <span class="name-mark__dot"></span>
      <span>Thomas G Ward</span>
    </div>

    <p class="owner-phone">
      <svg viewBox="0 0 16 20" aria-hidden="true">
        <path d="M5 1 L8 5 Q8.5 6 7.5 7 L6 8 Q5.5 11 8 14 L9.5 13 Q10.5 12.3 11.3 13.2 L13.6 16.6 Q14 17.5 13 18.2 L11.5 19.2 Q9.5 20 7.5 18 Q3 13.5 2 8.5 Q1.5 5 3 2.2 L4 1.2 Q4.6 0.6 5 1 Z"/>
      </svg>
      041255503981
    </p>
    <p class="owner-address">14 elm rd riverton vic 4210</p>
  </header>

  <div class="signature" role="img" aria-label="Handwritten signature of Thomas Gale Ward"></div>
</main>
</body>
</html>
```